Initial website for sport tech startup

We are currently in the R&D phases of our new product. It’s a headband to prevent concussion in the soccer market initially.

We have 2 products, one that’s basic aimed at the youth market and the other more technology driven that’s aimed at the academies and professional market.

Initially the product will launch in the UK

Target Market(s)

Youth soccer players and parents in UK, Soccer Clubs, Federations.

Industry/Entity Type

Sporting Good

Coding

Coded - Design and coding required

Number of Pages Required

5+ page

Requirements
Must have
• Professional style that can be adapted and changed over the coming months.
Nice to have
• Ecommerce ability in the future.

```html
<!DOCTYPE html>
<html lang="en">
<head>
<meta charset="utf-8">
<title>Helmark – Bringing Safety to the Sports Concussion Debate</title>
<link rel="stylesheet" href="https://fonts.googleapis.com/css2?family=Poppins:wght@300;400;500;600;700;800&family=Roboto:wght@400;500&display=swap">
<style>
:root{
  --ink:#1f232a;
  --text:#3a3f47;
  --muted:#8a9099;
  --blue:#05658f;
  --sky:#1ab0ec;
  --pale:#eef1f6;
  --blog-bg:#f3f5f8;
  --footer:#2b2b2b;
  --footer-text:#b9bcc1;
  --band:#525a65;
  --band-dark:#2a3039;
  --white:#ffffff;
}
*{box-sizing:border-box;margin:0;padding:0}
html,body{width:1200px;height:3337px;overflow:hidden}
body{position:relative;background:var(--white);font-family:'Poppins',sans-serif;color:var(--text)}
.abs{position:absolute}

/* hero */
.hero-photo{left:0;top:0;width:646px;height:595px;
  background:linear-gradient(160deg,#3d4a55 0%,#6c7a84 35%,#c9c3bb 55%,#4c5a3b 85%,#3e6b2a 100%);
  clip-path:polygon(0 0,646px 0,646px 430px,522px 430px,522px 595px,0 595px)}
.hero-panel{left:550px;top:0;width:650px;height:595px;background:var(--pale);
  clip-path:polygon(96px 0,650px 0,650px 595px,0 595px,0 430px,96px 430px)}
.logo{font-family:'Poppins',sans-serif;font-weight:600;letter-spacing:1px;color:var(--white)}
.hero-logo{left:118px;top:38px;font-size:30px;line-height:44px}
.nav{left:692px;top:40px;width:333px;height:40px;background:var(--white);border-radius:20px;
  display:flex;align-items:center;gap:31px;padding-left:36px;font-size:13px;color:#6b7380}
.nav a{text-decoration:none;color:inherit;position:relative}
.nav .active{color:var(--ink);font-weight:500}
.nav .active::after{content:"";position:absolute;left:50%;bottom:-8px;width:3px;height:3px;margin-left:-1.5px;border-radius:50%;background:var(--ink)}
.cart{left:1048px;top:48px}
.cart-count{left:1066px;top:41px;width:15px;height:15px;border-radius:50%;background:var(--sky);color:var(--white);font-size:9px;text-align:center;line-height:15px}
.hero-title{left:118px;top:204px;font-size:38px;font-weight:800;line-height:48px;color:var(--white);text-transform:uppercase}
.btn{display:inline-block;border-radius:20px;font-size:13px;font-weight:500;text-align:center;text-decoration:none}
.btn-sky{background:var(--sky);color:var(--white);border:2px solid var(--white)}
.hero-btn{left:118px;top:442px;width:139px;height:39px;line-height:35px}
.product-image{background:linear-gradient(135deg,var(--band) 0%,#6b737e 50%,var(--band-dark) 100%);border-radius:24px}
.hero-band{left:434px;top:208px;width:526px;height:310px}

/* about */
.about-title{left:120px;top:702px;width:500px;font-size:23px;font-weight:600;line-height:37px;color:var(--ink);text-transform:uppercase}
.about-text{left:120px;top:802px;width:480px;font-family:'Roboto',sans-serif;font-size:15.5px;line-height:30px;color:#2f343b}
.about-text p+p{margin-top:16px}
.frame-lg{left:670px;top:680px;width:359px;height:340px;border:2px solid var(--blue)}
.photo-lg{left:683px;top:694px;width:335px;height:313px;background:linear-gradient(135deg,#5f7a4c,#a33a52 40%,#2d4fa0 65%,#6f8a5a)}
.frame-sm{left:622px;top:907px;width:215px;height:152px;border:2px solid var(--blue);background:var(--white)}
.photo-sm{left:630px;top:914px;width:200px;height:135px;background:linear-gradient(180deg,#8b98a8,#dfe3e8 40%,#4d7c36 60%,#3c6b2a)}

/* product info */
.info-band{left:0;top:1153px;width:1200px;height:525px;background:var(--blue)}
.section-title{width:1200px;left:0;text-align:center;font-size:30px;font-weight:400}
.info-title{top:1218px;color:var(--white)}
.info-title b{font-weight:700}
.card{top:1304px;width:222px;height:251px;background:var(--white);border:1px solid #cfe3a8;text-align:center}
.card .icon{position:absolute;left:86px;top:36px}
.card h3{position:absolute;left:0;width:100%;top:128px;font-size:15.5px;font-weight:600;color:var(--ink)}
.card p{position:absolute;left:32px;width:158px;top:168px;font-size:13px;line-height:22px;color:#5a616b}
.card.raised h3{top:100px}
.card.raised p{top:140px}
.card-arrow{left:95px;top:198px;width:32px;height:32px;border-radius:50%;background:var(--blue)}

/* headband */
.hb-title{top:1735px;font-weight:700;color:var(--ink)}
.hb-rule{left:597px;top:1783px;width:1px;height:27px;background:#9aa0a8}
.hb-shape{left:340px;top:1838px;width:502px;height:280px}
.shop-btn{left:531px;top:2132px;width:138px;height:37px;line-height:33px}
.dot{top:2215px;width:9px;height:9px;border-radius:50%;background:#c4c9cf}
.dot.on{background:var(--blue)}

/* blog */
.blog-band{left:0;top:2278px;width:1200px;height:592px;background:var(--blog-bg)}
.blog-title{top:2325px;font-size:42px;color:var(--blue)}
.blog-title b{color:var(--ink);font-weight:600}
.blog-sub{top:2384px;font-size:19px;color:#8d939b;font-weight:300}
.blog-photo{top:2445px;width:411px;height:245px}
.photo-keeper{left:146px;background:linear-gradient(135deg,#2b3a4e,#8d99a6 45%,#e6e8ea 60%,#3a4555)}
.photo-kick{left:618px;background:linear-gradient(135deg,#6e1b22,#b43a3d 30%,#d7c3a4 55%,#2d4a22 85%)}
.blog-card{top:2635px;width:289px;height:88px;background:var(--white);box-shadow:0 4px 14px rgba(0,0,0,.06)}
.blog-card .excerpt{position:absolute;left:19px;top:17px;width:215px;font-size:10.5px;font-weight:600;line-height:19px;color:#2b2f66}
.blog-card .tag{position:absolute;left:57px;top:60px;font-size:12px;color:#777}
.blog-card .tag-line{position:absolute;left:19px;top:67px;width:26px;height:2px;background:#3bb54a}
.blog-card.plain .tag-line{background:#cfd3d8}
.blog-card .go{position:absolute;right:18px;top:30px;width:30px;height:30px;border-radius:50%;border:1px solid #e1e4e8}
.view-btn{left:520px;top:2764px;width:160px;height:37px;line-height:33px;border:2px solid #6b7380;color:#3c4450;background:transparent}

/* newsletter */
.news-title{top:2918px;font-size:31px;color:var(--ink)}
.news-field{left:259px;top:3004px;width:677px;height:22px;border-bottom:1px solid #cfd3d8;font-size:10px;color:#b0b4ba;display:flex;justify-content:space-between}

/* footer */
.footer{left:0;top:3087px;width:1200px;height:250px;background:var(--footer)}
.f-head{top:3132px;font-size:15px;font-weight:400;color:#e4e6e9}
.f-text{font-size:13px;color:var(--footer-text);line-height:22px}
.f-div{top:3138px;width:1px;height:140px;background:#3f3f3f}
.f-links{left:530px;top:3171px;font-size:13px;color:var(--footer-text);line-height:28.5px;list-style:none}
.f-logo{left:850px;top:3158px;font-size:30px;line-height:44px}
.socials{left:870px;top:3230px;display:flex;gap:16px}
.socials span{width:13px;height:13px;border-radius:50%;background:#9ca0a6}
</style>
</head>
<body>

<!-- hero -->
<div class="abs hero-photo" role="img" aria-label="Soccer player performing an overhead kick in a stadium"></div>
<div class="abs hero-panel"></div>
<div class="abs logo hero-logo">HELMARK</div>
<nav class="abs nav">
  <a class="active" href="#">Home</a><a href="#">Products</a><a href="#">Shop</a><a href="#">Contact</a>
</nav>
<svg class="abs cart" width="26" height="24" viewBox="0 0 26 24" fill="none" stroke="#8a9099" stroke-width="1.6" stroke-linejoin="round">
  <path d="M1 2h4l3 13h13l3-9H7"/><circle cx="10" cy="20" r="1.8"/><circle cx="19" cy="20" r="1.8"/>
</svg>
<div class="abs cart-count">0</div>
<h1 class="abs hero-title">Bringing safety<br>to the sports<br>concussion<br>debate</h1>
<a class="abs btn btn-sky hero-btn" href="#">Learn More</a>
<div class="abs product-image hero-band" role="img" aria-label="Product photo of the protective sports headband"></div>

<!-- about -->
<h2 class="abs about-title">Helmark – Bringing safety to the sports concussion debate</h2>
<div class="abs about-text">
  <p>Helmark is designing and developing head protectioHelmark protection products to reduce the likelihood of concussion when playing sports.</p>
  <p>Exploring and understanding medical insights, material science and composites research, current and former players experiences and governing bodies guidelines has allowed Helmark to develop the safety</p>
</div>
<div class="abs frame-lg"></div>
<div class="abs photo-lg" role="img" aria-label="Two soccer players heading the ball"></div>
<div class="abs frame-sm"></div>
<div class="abs photo-sm" role="img" aria-label="Injured player receiving attention on the pitch"></div>

<!-- product info -->
<div class="abs info-band"></div>
<h2 class="abs section-title info-title">Product <b>Info</b></h2>

<div class="abs card" style="left:240px">
  <svg class="icon" width="50" height="52" viewBox="0 0 50 52" fill="none" stroke="var(--blue)" stroke-width="1.8" stroke-linecap="round">
    <rect x="8" y="3" width="36" height="44" rx="3"/><path d="M15 13h22M15 20h22M15 27h14"/><path d="M4 36l7 8 13-16"/>
  </svg>
  <h3>Safety Tested</h3><p>Lorem Ipsum is simply dummy text of the</p>
</div>
<div class="abs card raised" style="left:489px;top:1308px;height:247px">
  <svg class="icon" width="50" height="46" viewBox="0 0 50 46" fill="none" stroke="var(--blue)" stroke-width="1.8" stroke-linecap="round" style="top:28px">
    <path d="M6 28 Q10 8 44 4 Q36 26 10 30 Z"/><path d="M10 30 L40 8"/><path d="M2 42h46"/><path d="M8 38h4M20 38h4M32 38h4"/>
  </svg>
  <h3>Light Weight</h3><p>Lorem Ipsum is simply dummy text of the</p>
  <span class="abs card-arrow"><svg width="32" height="32" viewBox="0 0 32 32" fill="none" stroke="#fff" stroke-width="1.8"><path d="M10 16h12M17 11l5 5-5 5"/></svg></span>
</div>
<div class="abs card" style="left:737px">
  <svg class="icon" width="52" height="52" viewBox="0 0 52 52" fill="none" stroke="var(--blue)" stroke-width="1.8" stroke-linecap="round">
    <path d="M10 46V24a12 12 0 0 1 24 0v22"/><rect x="4" y="30" width="36" height="14" rx="3"/><path d="M46 6v40M42 6h8M40 46h10"/>
  </svg>
  <h3>Comfortable</h3><p>Lorem Ipsum is simply dummy text of the</p>
</div>

<!-- headband -->
<h2 class="abs section-title hb-title">Headband</h2>
<div class="abs hb-rule"></div>
<div class="abs product-image hb-shape" role="img" aria-label="Product photo of the protective sports headband"></div>
<a class="abs btn btn-sky shop-btn" href="#">Shop Now</a>
<span class="abs dot" style="left:576px"></span><span class="abs dot on" style="left:595px"></span><span class="abs dot" style="left:614px"></span>

<!-- blog -->
<div class="abs blog-band"></div>
<h2 class="abs section-title blog-title">Our <b>Blog</b></h2>
<p class="abs section-title blog-sub">Lorem Ipsum is simply dummy text of the printing</p>
<div class="abs blog-photo photo-keeper" role="img" aria-label="Goalkeeper diving for the ball"></div>
<div class="abs blog-card" style="left:293px">
  <p class="excerpt">Lorem Ipsum is simply dummy text of the printing and typesetting</p><i class="tag-line"></i><span class="tag">Headband</span>
  <span class="go"><svg width="28" height="28" viewBox="0 0 28 28" fill="none" stroke="#3bb54a" stroke-width="1.5"><path d="M12 10l4 4-4 4"/></svg></span>
</div>
<div class="abs blog-photo photo-kick" role="img" aria-label="Player's boot on a soccer ball"></div>
<div class="abs blog-card plain" style="left:765px">
  <p class="excerpt">Lorem Ipsum is simply dummy text of the printing and typesetting</p><i class="tag-line"></i><span class="tag">Headband</span>
  <span class="go"><svg width="28" height="28" viewBox="0 0 28 28" fill="none" stroke="#b0b4ba" stroke-width="1.5"><path d="M12 10l4 4-4 4"/></svg></span>
</div>
<a class="abs btn view-btn" href="#">View More</a>

<!-- newsletter -->
<h2 class="abs section-title news-title">Join Our Newsletter</h2>
<div class="abs news-field"><span>Your email address</span><span>Subscribe</span></div>

<!-- footer -->
<footer class="abs footer"></footer>
<h4 class="abs f-head" style="left:153px">Contact Us</h4>
<p class="abs f-text" style="left:153px;top:3170px">Lorem Ipsum, is simply<br>dummy text of the</p>
<p class="abs f-text" style="left:153px;top:3230px">+xxxx xxxx xxxxx</p>
<p class="abs f-text" style="left:153px;top:3263px">xxxxxxx@helmark-mail.com</p>
<div class="abs f-div" style="left:403px"></div>
<h4 class="abs f-head" style="left:530px">Contact Us</h4>
<ul class="abs f-links"><li>Home</li><li>About</li><li>Shop</li><li>Contact</li></ul>
<div class="abs f-div" style="left:733px"></div>
<div class="abs logo f-logo">HELMARK</div>
<div class="abs socials"><span></span><span></span><span></span><span></span><span></span></div>

</body>
</html>
```